Every Shelf Set Neatly or ESN Organized needs a business card design. ESN Organized is a professi

We need a business card design that is clean, sharp and conveys a sense of organization. I already have a logo.

Target Market(s)

Families (specifically mothers), small business owners, parents, seniors

Industry/Entity Type

Business

Contact Information for Business Card

My website is www.esnorganized-example.com and my Facebook page is http://www.sociallink-example.com/everyshelfsetneatly. The phone number is 418-552-7094 and I want to be listed as Lorna M. Pelham, Owner

Requirements
Must have
• My logo.

```html
<!DOCTYPE html>
<html lang="en">
<head>
<meta charset="utf-8">
<title>ESN Organized – Business Card</title>
<link rel="stylesheet" href="https://fonts.googleapis.com/css2?family=Open+Sans:wght@300;400;600;700&display=swap">
<style>
  :root {
    --page-bg: #e6e6e4;
    --brand-blue: #1f86e0;
    --brand-blue-deep: #0d6cc4;
    --ink: #1b1b1b;
    --ink-soft: #4a4a4a;
    --card-white: #ffffff;
    --card-black: #050505;
    --back-text: #d8d8d8;
  }
  * { box-sizing: border-box; margin: 0; padding: 0; }
  html, body {
    width: 1200px; height: 843px; overflow: hidden;
    background: var(--page-bg);
    font-family: "Open Sans", Arial, sans-serif;
  }
  .stage {
    width: 1200px; height: 843px;
    display: flex; align-items: center; justify-content: center; gap: 40px;
  }
  .card {
    position: relative;
    width: 540px; height: 309px;
    border-radius: 4px;
    overflow: hidden;
    box-shadow: 0 10px 28px rgba(0,0,0,0.18);
  }

  /* Back side */
  .card-back {
    background: linear-gradient(160deg, #1a1a1a 0%, var(--card-black) 55%);
    display: flex; flex-direction: column; align-items: center; justify-content: center;
  }
  .back-mark {
    color: var(--brand-blue);
    font-weight: 300;
    font-size: 104px;
    letter-spacing: 4px;
    line-height: 1;
  }
  .back-web {
    margin-top: 26px;
    color: var(--back-text);
    font-size: 13px;
    letter-spacing: 6px;
  }

  /* Front side */
  .card-front {
    background: linear-gradient(135deg, var(--card-white) 0%, #f2f2f2 100%);
  }
  .front-logo {
    position: absolute; left: 34px; top: 32px;
    color: var(--brand-blue);
    font-weight: 400;
    font-size: 22px;
    letter-spacing: 1.5px;
  }
  .person { position: absolute; left: 34px; top: 100px; }
  .person-name {
    color: var(--brand-blue);
    font-weight: 700;
    font-size: 19px;
    letter-spacing: 0.5px;
  }
  .person-role {
    color: var(--ink);
    font-size: 12px;
    font-weight: 600;
    margin-top: 4px;
  }
  .contact-list {
    position: absolute; left: 34px; top: 176px;
    list-style: none;
  }
  .contact-item {
    display: flex; align-items: center; gap: 8px;
    color: var(--ink-soft);
    font-size: 14px;
    line-height: 23px;
  }
  .contact-icon { width: 13px; height: 13px; flex: none; }
  .corner-band {
    position: absolute;
    left: 300px; top: 215px;
    width: 440px; height: 170px;
    border-radius: 85px;
    background: linear-gradient(180deg, var(--brand-blue) 0%, var(--brand-blue-deep) 100%);
    transform: rotate(-33deg);
    transform-origin: left center;
  }
</style>
</head>
<body>
<main class="stage">
  <section class="card card-back" aria-label="Card back">
    <div class="back-mark">ESN</div>
    <div class="back-web">www.esnorganized-example.com</div>
  </section>

  <section class="card card-front" aria-label="Card front">
    <div class="front-logo">Every Shelf Set Neatly</div>

    <div class="person">
      <div class="person-name">LORNA M. PELHAM</div>
      <div class="person-role">OWNER</div>
    </div>

    <ul class="contact-list">
      <li class="contact-item">
        <svg class="contact-icon" viewBox="0 0 24 24" aria-hidden="true">
          <path fill="var(--brand-blue)" d="M6.6 10.8a15.1 15.1 0 0 0 6.6 6.6l2.2-2.2a1 1 0 0 1 1-.25 11.4 11.4 0 0 0 3.6.57 1 1 0 0 1 1 1V20a1 1 0 0 1-1 1A17 17 0 0 1 3 4a1 1 0 0 1 1-1h3.5a1 1 0 0 1 1 1c0 1.25.2 2.45.57 3.57a1 1 0 0 1-.25 1z"/>
        </svg>
        418-552-7094
      </li>
      <li class="contact-item">
        <svg class="contact-icon" viewBox="0 0 24 24" aria-hidden="true">
          <circle cx="12" cy="12" r="10" fill="var(--brand-blue)"/>
        </svg>
        www.esnorganized-example.com
      </li>
      <li class="contact-item">
        <svg class="contact-icon" viewBox="0 0 24 24" aria-hidden="true">
          <rect x="2" y="2" width="20" height="20" rx="3" fill="var(--brand-blue)"/>
        </svg>
        everyshelfsetneatly
      </li>
    </ul>

    <div class="corner-band" role="img" aria-label="Large blue paper clip graphic"></div>
  </section>
</main>
</body>
</html>
```